Design refresh / update on current website (design only)

I currently have this website - www.pulse-harbour.com and I would like a refresh / update on it
Primarily, I would like the events page re designed as that is the most important page -
www.pulse-harbour.com/events
I would like it done to look like this in terms of layout -
https://www.thebrightvaultrooms.com/club-events/
(But without looking like it is a direct copy)
But I do not like the more pastel type look of this example website, instead I would like a sharper more digital look and feel like it is at the moment or like -
https://orbitune.com/events
www.zqtfeast.com
https://www.palaceofechoes.com/club/
It MUST have that sharp digital look and feel
And to look at the top bit of the website with the following menu options -
HOME
EVENTS
SHOP
HIRE
EXPERIENCES
ARTIST BOOKINGS
CONTACT
I am thinking once this is nailed, the home page and rest of the site can then be worked on as a separate project
There is also a ''pulse rhythms for a pulse harbour'' slogan which I would like added somewhere or it can be saved for just the home page or the bottom of pages
I would also like a filter button on the events so you can filter by -
All Events
Festivals
Brunches
Clubs
Amsterdam
Abroad
Experiences
UK Tour
It must at the very least look of equal standard as the bright vault look and feel
Go with the rectangle buttons rather than the current ones and move away from the pink current colours to look a bit cooler

```html
<!DOCTYPE html>
<html lang="en">
<head>
<meta charset="utf-8">
<title>Pulse Harbour – Events</title>
<link href="https://fonts.googleapis.com/css2?family=Poppins:wght@400;500;600;700&display=swap" rel="stylesheet">
<style>
:root{
  --black:#05070b;
  --ink:#0e1218;
  --accent:#12a9e6;
  --accent-deep:#0b7fb3;
  --page:#f4f6f8;
  --white:#fff;
  --line:#cfd6dd;
  --muted:#4a5560;
}
*{margin:0;padding:0;box-sizing:border-box}
html,body{width:1200px;height:2745px;overflow:hidden}
body{position:relative;background:var(--page);font-family:'Poppins',sans-serif;color:var(--ink)}

/* header */
.site-header{position:absolute;left:0;top:0;width:1200px;height:75px;background:var(--black)}
.brand{position:absolute;left:60px;top:18px;color:var(--white);font-weight:700;font-size:30px;letter-spacing:1px;line-height:40px}
.main-nav{position:absolute;right:60px;top:30px;display:flex;gap:38px}
.main-nav a{color:var(--white);text-decoration:none;font-size:12.5px;letter-spacing:.3px}

/* hero */
.hero-band{position:absolute;left:0;top:75px;width:1200px;height:562px;background:var(--black)}
.hero-photo{position:absolute;left:60px;top:75px;width:1080px;height:562px;
  background:radial-gradient(ellipse at 60% 35%,#ff2a4a 0%,#b0102a 35%,#4a0612 70%,#1a0208 100%)}
.hero-mark{position:absolute;left:495px;top:221px;width:210px;height:72px;border:2px solid var(--white);
  display:flex;align-items:center;justify-content:center;color:var(--white);font-weight:600;font-size:18px;letter-spacing:1px}
.hero-title{position:absolute;left:0;width:1200px;top:316px;text-align:center;color:var(--white);font-weight:600;font-size:50px;line-height:60px}
.side-social{position:absolute;left:1158px;top:200px;width:24px}
.side-social .rule{width:1px;height:68px;background:var(--accent);margin:0 auto}
.side-social .sq{width:12px;height:12px;background:var(--white);margin:16px auto}
.side-social .sq.active{width:28px;height:28px;background:none;border:1.5px solid var(--accent);margin:10px auto}
.scroll-cue{position:absolute;left:36px;top:568px;width:48px;height:48px;border:1px dashed var(--white)}

/* events */
.section-title{position:absolute;left:0;width:1200px;top:681px;text-align:center;font-weight:600;font-size:34px;line-height:44px}
.section-title::before,.section-title::after{content:"";position:absolute;top:23px;width:55px;height:1px;background:#9aa4ad}
.section-title::before{left:342px}
.section-title::after{right:342px}
.search{position:absolute;left:217px;top:755px;width:453px;height:45px;border:1px solid var(--line);background:var(--white)}
.search span{position:absolute;left:15px;top:13px;font-size:13px;color:var(--muted)}
.search .go{position:absolute;right:3px;top:3px;width:41px;height:37px;background:var(--accent)}
.filter-btn{position:absolute;left:1012px;top:756px;width:128px;height:44px;background:var(--accent);color:var(--white);font-size:13px;display:flex;align-items:center;justify-content:center;gap:12px}

.event{position:absolute;left:223px;width:752px;height:334px}
.event .poster{position:absolute;left:0;top:0;width:363px;height:334px}
.event .panel{position:absolute;left:318px;top:19px;width:434px;height:297px;background:var(--white)}
.event .date{position:absolute;left:280px;top:119px;width:113px;height:105px;background:var(--accent);color:var(--white);text-align:center}
.date .day{display:block;font-size:14px;margin-top:14px}
.date .num{display:block;font-size:26px;font-weight:500;line-height:30px}
.date .mon{display:block;font-size:17px}
.event .info{position:absolute;left:440px;right:0;top:0;bottom:0;display:flex;flex-direction:column;justify-content:center}
.event h3{font-size:31px;font-weight:600;line-height:41px;text-transform:uppercase}
.event .venue{color:var(--accent-deep);font-size:16px;margin-top:6px;text-transform:uppercase}
.event .buy{display:inline-block;margin-top:20px;width:112px;height:37px;background:var(--accent);color:var(--white);font-size:12px;line-height:37px;text-align:center;align-self:flex-start}

.pager{position:absolute;top:2331px;left:533px;display:flex;gap:12px}
.pager span{width:37px;height:37px;border:1px solid var(--accent);font-size:13px;color:var(--muted);display:flex;align-items:center;justify-content:center}
.pager .on{background:var(--accent);color:var(--white)}

/* footer */
.site-footer{position:absolute;left:0;top:2425px;width:1200px;height:320px;background:var(--black);color:var(--white)}
.foot-brand{position:absolute;left:60px;top:58px;font-weight:600;font-size:22px;line-height:30px;display:flex;align-items:center;gap:10px}
.foot-brand i{display:block;width:26px;height:26px;border:2px solid var(--white)}
.slogan{position:absolute;left:60px;top:104px;font-size:16px;line-height:22px}
.foot-h{position:absolute;color:var(--accent);font-weight:600;font-size:16px}
.foot-p{position:absolute;font-size:12px;line-height:21px}
.mail-row{position:absolute;left:60px;top:188px;display:flex;align-items:center;gap:9px;font-size:12.5px}
.email-field{position:absolute;left:432px;top:144px;width:329px;height:34px;border:1px solid var(--white);font-size:12px;padding:9px 13px}
.subscribe{position:absolute;left:432px;top:193px;width:104px;height:37px;background:var(--accent);font-size:12px;display:flex;align-items:center;justify-content:center}
.foot-rule{position:absolute;left:0;top:282px;width:1200px;height:1px;background:#222a33}
.copyright{position:absolute;left:60px;top:295px;font-size:12px}
.foot-social{position:absolute;right:60px;top:290px;display:flex;gap:12px}
.foot-social span{width:28px;height:28px;border:1.5px solid var(--white)}
.foot-social .on{background:var(--accent);border-color:var(--accent)}
</style>
</head>
<body>

<header class="site-header">
  <div class="brand">PULSE HARBOUR</div>
  <nav class="main-nav">
    <a>HOME</a><a>EVENTS</a><a>SHOP</a><a>HIRE</a><a>EXPERIENCES</a><a>ARTIST BOOKINGS</a><a>CONTACT</a>
  </nav>
</header>

<div class="hero-band"></div>
<div class="hero-photo" role="img" aria-label="Crowd at a club night under red and blue stage lights"></div>
<div class="hero-mark">PULSE HARBOUR</div>
<h1 class="hero-title">Pulse rhythms for a pulse Harbour</h1>
<div class="side-social" aria-label="Social links">
  <div class="rule"></div>
  <div class="sq"></div>
  <div class="sq active"></div>
  <div class="sq"></div>
  <div class="sq"></div>
  <div class="rule"></div>
</div>
<div class="scroll-cue">
  <svg width="46" height="46" viewBox="0 0 46 46"><path d="M23 14v17M18 26l5 5 5-5" stroke="#fff" stroke-width="1.5" fill="none"/></svg>
</div>

<h2 class="section-title">PULSE HARBOUR EVENTS</h2>
<div class="search"><span>Search Events</span>
  <div class="go"><svg width="41" height="37" viewBox="0 0 41 37"><circle cx="19" cy="17" r="7" stroke="#fff" stroke-width="2" fill="none"/><path d="M24 22l6 6" stroke="#fff" stroke-width="2"/></svg></div>
</div>
<div class="filter-btn">
  <svg width="24" height="18" viewBox="0 0 24 18"><g stroke="#fff" stroke-width="1.5"><path d="M1 3h22M1 9h22M1 15h22"/><rect x="14" y="1" width="4" height="4" fill="#12a9e6"/><rect x="5" y="7" width="4" height="4" fill="#12a9e6"/><rect x="12" y="13" width="4" height="4" fill="#12a9e6"/></g></svg>
  Filter By
</div>

<article class="event" style="top:860px">
  <div class="poster" role="img" aria-label="DJ on stage under green lasers" style="background:radial-gradient(circle at 30% 30%,#4dffb0,#0e9a5a 45%,#04301c 100%)"></div>
  <div class="panel"></div>
  <div class="date"><span class="day">Sat</span><span class="num">26</span><span class="mon">Nov 2022</span></div>
  <div class="info"><h3>Pulse Harbour<br>Milton Keynes</h3><div class="venue">Hall Eleven</div><span class="buy">BUY TICKETS</span></div>
</article>

<article class="event" style="top:1224px">
  <div class="poster" role="img" aria-label="Event poster with hosts for the club tour night" style="background:linear-gradient(160deg,#2fae6a,#0c5a34 55%,#021a0e)"></div>
  <div class="panel"></div>
  <div class="date"><span class="day">Sat</span><span class="num">26</span><span class="mon">Nov 2022</span></div>
  <div class="info"><h3>Pulse Harbour<br>Biggleswade</h3><div class="venue">Biggleswade</div><span class="buy">BUY TICKETS</span></div>
</article>

<article class="event" style="top:1588px">
  <div class="poster" role="img" aria-label="Christmas party brunch poster in red and green" style="background:linear-gradient(120deg,#d9232e 0%,#c81e2a 50%,#5aa82e 100%)"></div>
  <div class="panel"></div>
  <div class="date"><span class="day">Sat</span><span class="num">3</span><span class="mon">Dec 2022</span></div>
  <div class="info"><h3>Pulse Harbour<br>Christmas<br>Brunch</h3><div class="venue">Veranda , Kings Cross</div><span class="buy">BUY TICKETS</span></div>
</article>

<article class="event" style="top:1952px">
  <div class="poster" role="img" aria-label="Bingo and Christmas brunch poster in orange, red and green" style="background:linear-gradient(120deg,#f28a1c 0%,#e0402a 55%,#58a530 100%)"></div>
  <div class="panel"></div>
  <div class="date" style="left:274px"><span class="day">Sat</span><span class="num">10</span><span class="mon">Dec 2022</span></div>
  <div class="info" style="left:434px"><h3>Pulse Harbour<br>Milton Keynes</h3><div class="venue">Hall Eleven</div><span class="buy">BUY TICKETS</span></div>
</article>

<div class="pager"><span>01</span><span class="on">02</span><span>03</span></div>

<footer class="site-footer">
  <div class="foot-brand"><i></i>PULSE HARBOUR</div>
  <div class="slogan">pulse rhythms for a pulse harbour</div>
  <div class="foot-h" style="left:61px;top:160px">CONTACT US</div>
  <div class="mail-row">
    <svg width="18" height="13" viewBox="0 0 18 13"><rect x=".5" y=".5" width="17" height="12" fill="none" stroke="#fff"/><path d="M.5 .5l8.5 7 8.5-7" fill="none" stroke="#fff"/></svg>
    support@pulse-harbour.com
  </div>

  <div class="foot-h" style="left:432px;top:61px">KEEP UP TO DATE</div>
  <p class="foot-p" style="left:432px;top:97px;width:310px">Sign Up to receive exclusive discounts &amp; pre sale links before anyone else!</p>
  <div class="email-field">E-mail</div>
  <div class="subscribe">SUBSCRIBE</div>

  <div class="foot-h" style="left:848px;top:61px">QUICK LINKS</div>
  <p class="foot-p" style="left:848px;top:97px">Work With Us<br><span style="display:block;margin-top:7px">Privacy Policy</span></p>

  <div class="foot-rule"></div>
  <div class="copyright">© Pulse Harbour 2022. All Right Reserved.</div>
  <div class="foot-social" aria-label="Social links"><span></span><span></span><span class="on"></span><span></span></div>
</footer>

</body>
</html>
```